Business Card Design For A Cajun Seafood Restaurant

We are opening a cajun seafood restaurant in a week. We mainly serve cajun seafood which is orginally from Louisiana. We want design on both sides of a business card. I have menu on the website. You can go to www.reednkettle.example to check out our menu.

Restaurant name: Reed N' Kettle
Phone: +1 (555) 304-7712
Address: 48206 Ludlow Row, #7, Bexmoor Flats, Ca90000
Email: reednkettle@mailbox.example
Website: www.reednkettle.example

Maybe add social media icons (facebook, instagram) if looks nice on the business card.
facebook.com/reednkettle
instagram.com/reednkettle or @reednkettle

Attached is the logo and other business card samples that I like.

```html
<!DOCTYPE html>
<html lang="en">
<head>
<meta charset="utf-8">
<title>Reed N' Kettle — Business Card</title>
<link href="https://fonts.googleapis.com/css2?family=Source+Sans+3:wght@400;600;700&display=swap" rel="stylesheet">
<style>
  :root {
    --backdrop: #c8c8c8;
    --card: #2e2f33;
    --card-edge: #3a3b40;
    --brand-yellow: #f6c500;
    --accent-orange: #e8720c;
    --text-light: #f2f2f2;
    --divider: #6a6b70;
    --crab-light: #f59a2a;
    --crab-dark: #d95f0a;
  }
  * { box-sizing: border-box; margin: 0; padding: 0; }
  html, body {
    width: 1200px; height: 900px; overflow: hidden;
    background: var(--backdrop);
    font-family: "Source Sans 3", "Myriad Pro", Arial, sans-serif;
  }
  .stage { position: relative; width: 1200px; height: 900px; }
  .card {
    position: absolute; top: 271px; width: 457px; height: 281px;
    background: var(--card); border-radius: 14px;
    box-shadow: 0 0 0 1px var(--card-edge);
  }
  .card--front { left: 137px; }
  .card--back { left: 626px; }

  .mascot {
    position: absolute; border-radius: 50%;
    background: radial-gradient(circle at 50% 40%, var(--crab-light), var(--crab-dark) 70%, transparent 72%);
  }
  .card--front .mascot { left: 30px; top: 50px; width: 200px; height: 190px; }
  .card--back .mascot { left: 172px; top: 58px; width: 128px; height: 112px; }

  .divider {
    position: absolute; left: 245px; top: 60px; width: 1px; height: 162px;
    background: linear-gradient(var(--card), var(--divider), var(--card));
  }
  .details { position: absolute; left: 261px; top: 45px; color: var(--text-light); }
  .brand-name {
    font-weight: 700; font-size: 21px; color: var(--brand-yellow);
    letter-spacing: 0.3px; line-height: 1;
  }
  .contact-list { list-style: none; margin-top: 22px; font-size: 13px; line-height: 17.5px; }
  .contact-list li { display: flex; align-items: center; gap: 7px; }
  .contact-list svg { width: 10px; height: 10px; fill: var(--accent-orange); flex: none; }
  .address { margin-top: 19px; font-size: 13px; line-height: 17.5px; }
  .social {
    margin-top: 21px; display: flex; align-items: center; gap: 6px;
    font-size: 16px; font-weight: 700;
  }
  .social .marker { width: 13px; height: 13px; border-radius: 2px; background: var(--brand-yellow); }

  .back-lockup {
    position: absolute; left: 0; right: 0; top: 168px; text-align: center;
  }
  .back-lockup .brand-name { font-size: 26px; }
  .tagline {
    margin-top: 8px; font-size: 12px; font-weight: 700; letter-spacing: 0.8px;
    color: var(--text-light);
  }
</style>
</head>
<body>
<main class="stage">
  <section class="card card--front">
    <div class="mascot" role="img" aria-label="Illustrated orange crab mascot holding a yellow corn cob"></div>
    <div class="divider"></div>
    <div class="details">
      <h1 class="brand-name">REED N' KETTLE</h1>
      <ul class="contact-list">
        <li><svg viewBox="0 0 10 10"><path d="M2 0.5 L3.6 2.6 L2.8 3.6 Q4 6 6.4 7.2 L7.4 6.4 L9.5 8 L8.2 9.5 Q3 9 0.5 1.8 Z"/></svg>+1 (555) 304-7712</li>
        <li><svg viewBox="0 0 10 10"><rect x="0.5" y="2" width="9" height="6.5"/><path d="M0.5 2 L5 5.5 L9.5 2" fill="none" stroke="#2e2f33" stroke-width="1"/></svg>reednkettle@mailbox.example</li>
        <li><svg viewBox="0 0 10 10"><circle cx="5" cy="5" r="4.5"/></svg>www.reednkettle.example</li>
      </ul>
      <p class="address">48206 Ludlow Row,<br>#7, Bexmoor Flats, Ca90000</p>
      <p class="social"><span class="marker"></span>/reednkettle</p>
    </div>
  </section>

  <section class="card card--back">
    <div class="mascot" role="img" aria-label="Illustrated orange crab mascot holding a yellow corn cob"></div>
    <div class="back-lockup">
      <h2 class="brand-name">REED N' KETTLE</h2>
      <p class="tagline">CAJUN SEAFOOD HOUSE</p>
    </div>
  </section>
</main>
</body>
</html>
```